kmvalerohub website

I need a new homepage design for my current website at www.KMValeroHub.com. I want someone to look at my current website and develop a more appealing homepage... right now the colors don't blend very well and it needs a facelift

Reason: This has been extended to September 10th

```html
<!DOCTYPE html>
<html lang="en">
<head>
<meta charset="utf-8">
<title>KM Valero – Home</title>
<link rel="stylesheet" href="https://fonts.googleapis.com/css2?family=Oswald:wght@300;400;500&family=Open+Sans:wght@400;600&display=swap">
<style>
:root{
  --ink:#333333;
  --dark:#2f2f2f;
  --pink:#d5105d;
  --paper:#ebebeb;
  --white:#ffffff;
  --grey:#555555;
  --footer-text:#bdbdbd;
}
*{margin:0;padding:0;box-sizing:border-box}
html,body{width:1029px;height:1200px;overflow:hidden}
body{position:relative;background:var(--paper);font-family:"Open Sans",sans-serif;color:var(--ink)}
.abs{position:absolute}
.header{left:0;top:0;width:1029px;height:124px;background:var(--dark);border-bottom:4px solid var(--pink)}
.logo{left:111px;top:28px;font-family:"Oswald",sans-serif;font-weight:400;font-size:24px;color:var(--white);letter-spacing:1px}
.nav{right:111px;top:42px;display:flex;gap:30px;font-family:"Oswald",sans-serif;font-size:15px;color:var(--white);list-style:none}
.nav li.active{color:var(--pink)}
.hero{left:111px;top:80px;width:807px;height:327px;background:var(--white);padding:4px;box-shadow:0 1px 4px rgba(0,0,0,.3)}
.hero-inner{position:relative;width:100%;height:100%;background:#000;overflow:hidden}
.hero-photo{position:absolute;left:400px;top:0;right:0;bottom:0;background:linear-gradient(90deg,#0a0a0a 0%,#5a1a1a 45%,#b52525 75%,#7a1515 100%)}
.hero-book{position:absolute;left:240px;top:130px;width:145px;height:185px;background:linear-gradient(160deg,#f6d0de,#e06a98)}
.hero-copy{position:absolute;left:30px;top:34px;font-family:"Oswald",sans-serif;color:var(--white)}
.hero-copy .l1{font-size:29px;font-weight:400}
.hero-copy .l1 em{font-style:normal;font-weight:500}
.hero-copy .l2{font-size:52px;font-weight:400;color:var(--pink);line-height:1.05;margin-top:2px}
.hero-copy .l3{font-size:28px;margin-top:2px}
.btn{display:inline-block;background:var(--pink);color:var(--white);font-family:"Oswald",sans-serif;font-size:17px;padding:4px 16px}
.hero-copy .btn{margin-top:22px}
.dots{position:absolute;left:31px;top:286px;display:flex;gap:4px}
.dots span{width:11px;height:11px;border-radius:50%;background:#9a9a9a}
.dots span:first-child{background:#fff}
.report{left:0;top:431px;width:1029px;height:185px;background:var(--pink);color:var(--white);text-align:center}
.report h2{font-family:"Oswald",sans-serif;font-weight:400;font-size:22px;margin-top:12px}
.report h3{font-weight:600;font-size:17px;margin-top:6px;letter-spacing:.5px}
.report p{font-size:11.5px}
.report-cover{top:48px;width:72px;height:96px;background:linear-gradient(160deg,#ffffff,#3a7bc8);box-shadow:2px 2px 4px rgba(0,0,0,.3)}
.form{left:249px;top:107px;display:flex;gap:17px}
.field{width:189px;height:26px;background:var(--white);color:#888;font-size:11.5px;text-align:left;padding:5px 11px}
.subscribe{width:121px;height:26px;background:var(--dark);font-size:12px;font-weight:600;letter-spacing:1px;padding-top:5px}
.privacy{left:0;width:1029px;top:144px;font-size:10.5px!important;line-height:1.4}
.about{left:111px;top:642px;width:807px;text-align:center}
.about h2{font-family:"Oswald",sans-serif;font-weight:400;font-size:22px}
.about h2 span,.card h2 span,.seen h2 span{color:var(--pink)}
.about p{font-size:11.3px;line-height:20px;margin-top:4px;color:var(--grey)}
.card{top:785px;height:182px;background:var(--white);border:2px solid var(--pink)}
.product{left:111px;width:394px}
.product-cover{left:22px;top:10px;width:95px;height:160px;background:linear-gradient(170deg,#f0f5e8,#7fb54a)}
.product-copy{left:143px;top:24px;font-family:"Oswald",sans-serif;color:var(--ink)}
.product-copy .a{font-size:20px}
.product-copy .a span,.product-copy .b span{color:var(--pink)}
.product-copy .b{font-size:20px;line-height:1}
.product-copy .b span{font-size:36px}
.product-copy .c{font-size:19px;margin-top:4px}
.product-copy .btn{margin-top:10px}
.stories{left:523px;width:395px;padding:12px 18px}
.card h2{font-family:"Oswald",sans-serif;font-weight:400;font-size:22px}
.quote{position:relative;font-size:11.5px;line-height:20px;color:var(--grey);margin-top:8px;text-indent:34px}
.qmark{position:absolute;font-family:Georgia,serif;font-size:46px;color:#9a9a9a;line-height:1}
.author{color:var(--pink);font-size:11.5px;font-weight:600;margin-top:10px}
.rule{left:111px;width:807px;height:1px;background:#b9b9b9}
.seen h2{font-family:"Oswald",sans-serif;font-weight:400;font-size:22px}
.badge{top:1004px;width:122px;height:53px;background:var(--white);border:1px solid #cfcfcf;display:flex;align-items:center;justify-content:center;font-family:"Open Sans",sans-serif;font-weight:600;font-size:18px;color:var(--ink)}
.footer{left:0;top:1093px;width:1029px;height:107px;background:var(--dark)}
.fnav{left:111px;top:24px;font-family:"Oswald",sans-serif;font-weight:300;font-size:12px;color:var(--footer-text)}
.copy{left:111px;top:65px;font-family:"Oswald",sans-serif;font-weight:300;font-size:11px;color:var(--footer-text)}
.copy span{color:var(--pink)}
.social{top:22px;display:flex;align-items:center;gap:5px;font-size:11px;color:var(--footer-text)}
.social i{display:block;width:30px;height:30px;border-radius:50%}
</style>
</head>
<body>
<header class="abs header">
  <div class="abs logo">KM Valero</div>
  <ul class="abs nav">
    <li class="active">HOME</li><li>ABOUT</li><li>PRODUCTS</li><li>BLOG</li><li>FORUM</li><li>MEDIA ROOM</li><li>SUCCESS STORIES</li>
  </ul>
</header>

<section class="abs hero">
  <div class="hero-inner">
    <div class="hero-photo" role="img" aria-label="Portrait of the author in a red dress seated on a red chair"></div>
    <div class="hero-book" role="img" aria-label="Stack of the author's weight-loss book"></div>
    <div class="hero-copy">
      <div class="l1"><em>Discover</em> Secrets to a</div>
      <div class="l2">SLIMMER SEXIER</div>
      <div class="l3">&amp; Healthier you!</div>
      <span class="btn">Read Details</span>
    </div>
    <div class="dots"><span></span><span></span><span></span><span></span></div>
  </div>
</section>

<section class="abs report">
  <div class="abs report-cover" style="left:134px" role="img" aria-label="Free report cover"></div>
  <div class="abs report-cover" style="left:821px" role="img" aria-label="Free report cover"></div>
  <h2>FREE REPORT</h2>
  <h3>"5 Reasons You Can't Lose Weight!"</h3>
  <p>Just enter your name and email below to get instant access to this 30 page report absolutely FREE!</p>
  <div class="abs form">
    <div class="field">Name</div>
    <div class="field">Email Address</div>
    <div class="subscribe">SUBSCRIBE</div>
  </div>
  <p class="abs privacy"><strong>E-mail Privacy:</strong><br>Sign up with complete confidence! We will never sell, rent, lease, or share your information with anyone.</p>
</section>

<section class="abs about">
  <h2>About <span>KM VALERO</span> Website</h2>
  <p>KM Valero is a nutritionist and certified weight-loss expert, passionate relationship/life coach, and inspirational speaker. She has been featured on The Dawn Rivers Morning Show, The Carl Benton Show, The Lena Hart Show, and The Ray Calloway Show.</p>
  <p>KM has made appearances on the ABN, KTV, SNC, BizOne and Metro Network television stations, as well as in the pages of Poise, Radiance, Body and Spirit, and Family Living Journal.</p>
</section>

<section class="abs card product">
  <div class="abs product-cover" role="img" aria-label="Green juice cleanse book cover"></div>
  <div class="abs product-copy">
    <div class="a">The <span>10-Day</span> Green</div>
    <div class="b"><span>Juice</span> Cleanse</div>
    <div class="c">Lose Up to 15 Pounds in 10 Days!</div>
    <span class="btn">Available Now</span>
  </div>
</section>

<section class="abs card stories">
  <h2>Success <span>Stories</span></h2>
  <div class="quote"><span class="qmark" style="left:0;top:-6px;text-indent:0">&ldquo;</span>DAY 10!!!! Feeling super excited at how far I've come!!!! I've lost 14 pounds!!!! It's amazing, and I definitely intend to do this again! THANKS, KM! I'm taking control of my life again and it feels AWESOME!!...<span class="qmark" style="left:100px;top:58px;text-indent:0">&rdquo;</span></div>
  <div class="author">-Tia R.</div>
</section>

<div class="abs rule" style="top:990px"></div>
<div class="abs seen" style="left:111px;top:1013px"><h2>As <span>Seen</span> on:</h2></div>
<div class="abs badge" style="left:232px">Signal</div>
<div class="abs badge" style="left:373px">Metro</div>
<div class="abs badge" style="left:514px">Airwave</div>
<div class="abs badge" style="left:655px">Poise</div>
<div class="abs badge" style="left:796px">ABN</div>
<div class="abs rule" style="top:1069px"></div>

<footer class="abs footer">
  <div class="abs fnav">HOME / PRODUCTS / ABOUT / BLOG / FORUM / MEDIA ROOM / SUCCESS STORIES</div>
  <div class="abs copy">COPYRIGHT © 2014. <span>KM VALERO</span>. ALL RIGHT RESERVED | PRIVACY POLICY | TERMS OF USE | DISCLAIMER</div>
  <div class="abs social" style="left:800px"><i style="background:#4a6ea0"></i>Circle</div>
  <div class="abs social" style="left:866px"><i style="background:#4ab3c4"></i>Chirp</div>
</footer>
</body>
</html>
```